Maplecrest Cove Retreat Wedding and Event Venue

We are looking for a webpage for our Wedding and Event Venue just opened up in Eastern San Diego CA. It is out of a private home that has a very photogenic backyard including grapevines and orchard trees, a 15 ft waterfall into a pool and market lights hanging from trees, all connected by paved stone and compacted dirt paths

We are looking for something that will be very bright, warm and inviting to our clients. The clientele will be mostly couples between 22 and 35 years of age for the weddings and planners/executives age 22-60 for our corporate events.

We would like a rustic Outdoor look as that is what our venue showcases. You can see our facebook Here: https://www.facebook.com/MaplecrestCoveRetreat/

We would like for the pictures on the facebook to be used on the page. The google drive where most of them are located is here for full file sizes https://files.examplecloud.net/open?id=7Q-9Kpt-M2xvaT8LwQeRTp4-DN5H

We would like to see designs that go with the colors of our logo and that included stone, wood, and grapevine textures as well as anything else rustic such as Market-lights.

The final design should be welcoming for newly engaged couples and corporations/companies who would like to book an outdoor venue for their wedding or next event. There can even be a simple first page with separate tabs for weddings and events that will be able to be more specially focused to the clients.

We would also like the option to be able to edit the pictures we place on the site seasonally as we would like our pictures to reflect our clients

Target Market(s)

Engaged couples age 22-35 and corporate planners/executives age 22-60

Industry/Entity Type

Events

Font styles to use
Script

Requirements
Must have
• Rustic Look, (wood, stone, wine vines/barrels, market lights, mason jars, etc)
• tab pages/sub pages for "About us", "Packages", "Pricing", "Gallery" (we must be able to put our pictures here from all our events), "What makes us Unique", "Contact us" that we are able to enter information into
Nice to have
• Colors matching our logo, Pictures from our Facebook page (listed in brief)
Should not have
• Corporate Look

```html
<!DOCTYPE html>
<html lang="en">
<head>
<meta charset="utf-8">
<title>Maplecrest Cove Retreat Wedding and Event Venue</title>
<link rel="stylesheet" href="https://fonts.googleapis.com/css2?family=Open+Sans:wght@400;600&family=Oswald:wght@500&display=swap">
<style>
:root{
  --gold:#b89a52;
  --gold-dark:#a8894a;
  --ink:#222222;
  --text:#555555;
  --white:#ffffff;
  --wood-light:#f1f0ed;
  --wood-mid:#e4e3df;
  --stone:#9d9d9d;
  --stone-dark:#8a8a8a;
  --sage:#c2ccc3;
  --sage-dark:#6f8a72;
  --linen:#ece6d8;
  --black:#0c0c0c;
  --btn-black:#1d1d1d;
}
*{box-sizing:border-box;margin:0;padding:0}
html,body{width:1200px;height:2946px;overflow:hidden}
body{position:relative;font-family:"Open Sans",Arial,sans-serif;color:var(--text);background:var(--wood-light)}
.abs{position:absolute}
.wood{background:linear-gradient(180deg,var(--wood-light),var(--wood-mid) 50%,var(--wood-light))}

/* header */
.site-header{left:0;top:0;width:1200px;height:130px;z-index:3}
.brand{left:0;width:1200px;top:44px;text-align:center;font-size:20px;font-weight:600;letter-spacing:3px;color:var(--gold);text-transform:uppercase}
.social-top{left:952px;top:44px;display:flex;gap:14px}
.social-top span{width:22px;height:22px;border-radius:50%;background:var(--gold);display:block}
.header-divider{left:1064px;top:34px;width:2px;height:44px;background:#555}
.search{left:1080px;top:45px}

/* hero */
.hero{left:0;top:130px;width:1200px;height:483px;background:linear-gradient(100deg,#d9cfb8 0%,#6f5a4a 30%,#c9a48c 48%,#efe1d3 62%,#e6e0d4 100%)}
.menu-panel{left:86px;top:47px;width:234px;height:287px;background:var(--white);box-shadow:0 2px 8px rgba(0,0,0,.25)}
.menu-close{left:12px;top:10px}
.menu-list{list-style:none;position:absolute;left:0;top:22px;width:234px;text-align:center;font-size:14px;color:#333}
.menu-list li{height:35px;line-height:35px}
.menu-list li.active{color:var(--gold)}
.hero-caption{left:86px;top:314px;width:470px;height:126px;background:linear-gradient(90deg,rgba(184,154,82,.95) 0%,rgba(184,154,82,.9) 45%,rgba(184,154,82,0) 85%)}
.hero-title{left:24px;top:20px;font-family:"Oswald",Arial,sans-serif;font-weight:500;font-size:38px;line-height:48px;color:var(--white);white-space:nowrap}
.hero-sub{left:20px;top:74px;font-size:25px;line-height:34px;color:var(--white);white-space:nowrap}
.slider-arrows{left:1064px;top:432px;display:flex;gap:4px}
.slider-arrows span{width:24px;height:24px;border-radius:50%;background:#555;display:flex;align-items:center;justify-content:center}

/* intro band */
.intro-band{left:0;top:613px;width:1200px;height:137px;background:linear-gradient(180deg,var(--stone),var(--stone-dark))}
.intro-text{left:114px;top:40px;width:664px;font-size:13px;line-height:20px;color:#f3f3f3}
.btn-contact{left:858px;top:45px;width:210px;height:53px;background:var(--btn-black);color:var(--white);font-size:20px;line-height:53px;text-align:center;border-radius:2px}

/* packages */
.packages{left:0;top:750px;width:1200px;height:519px}
.section-title{left:0;width:1200px;text-align:center;font-size:34px;color:var(--ink)}
.package-card{top:146px;width:312px;height:292px;background:var(--white);box-shadow:0 2px 6px rgba(0,0,0,.15)}
.package-photo{left:0;top:0;width:312px;height:165px}
.package-name{left:0;top:184px;width:312px;text-align:center;font-size:18px;color:var(--ink)}
.package-text{left:20px;top:212px;width:272px;text-align:center;font-size:13px;line-height:19px}
.package-more{left:0;top:255px;width:312px;text-align:center;font-size:12px;color:var(--gold)}

/* about */
.about{left:0;top:1269px;width:1200px;height:548px;background:var(--sage)}
.about-photo{left:461px;top:102px;width:607px;height:365px;background:linear-gradient(135deg,#6e6a5e,#9a3a3a 45%,#d8d2c4 70%,#4c5a3e)}
.text-box{background:var(--white);box-shadow:0 3px 10px rgba(0,0,0,.2);z-index:2}
.about-box{left:130px;top:157px;width:514px;height:255px}
.box-title{font-size:29px;color:var(--ink);white-space:nowrap}
.box-text{font-size:14px;line-height:22px}
.btn-small{height:36px;line-height:36px;text-align:center;color:var(--white);font-size:14px;border-radius:2px}

/* testimonial */
.testimonial{left:0;top:1817px;width:1200px;height:294px}
.quote-text{left:150px;top:72px;width:900px;text-align:center;font-size:22px;line-height:34px;color:#444}
.quote-author{left:0;top:188px;width:1200px;text-align:center;font-size:18px;color:var(--gold)}

/* unique */
.unique{left:0;top:2111px;width:1200px;height:554px;background:linear-gradient(180deg,var(--linen),#e3dccb)}
.unique-photo{left:132px;top:91px;width:608px;height:365px;background:linear-gradient(120deg,#e4d6c4,#8a2c30 40%,#c89e88 65%,#6a4638)}
.unique-box{left:552px;top:146px;width:514px;height:255px;text-align:right}

/* footer */
.site-footer{left:0;top:2665px;width:1200px;height:281px;background:var(--black)}
.footer-brand{left:0;top:52px;width:1200px;text-align:center;font-size:22px;line-height:30px;font-weight:600;letter-spacing:3px;color:var(--gold);text-transform:uppercase}
.footer-nav{left:0;top:122px;width:1200px;text-align:center;font-size:17px;line-height:24px;color:var(--white)}
.footer-nav span.sep{margin:0 14px}
.footer-social{left:508px;top:169px;display:flex;gap:38px}
.footer-social span{width:36px;height:36px;border-radius:50%;background:#3a3a3a;display:block}
.footer-social span:first-child{background:#7d9a85}
.copyright{left:0;top:226px;width:1200px;text-align:center;font-size:12px;color:#ddd}
</style>
</head>
<body>

<header class="site-header abs wood">
  <div class="brand abs">Maplecrest Cove Retreat</div>
  <div class="social-top abs" aria-label="Social links"><span></span><span></span><span></span></div>
  <div class="header-divider abs"></div>
  <svg class="search abs" width="24" height="24" viewBox="0 0 24 24" aria-label="Search"><circle cx="10" cy="10" r="7" fill="none" stroke="#222" stroke-width="2.6"/><line x1="15" y1="15" x2="22" y2="22" stroke="#222" stroke-width="3" stroke-linecap="round"/></svg>
  <nav class="menu-panel abs">
    <svg class="menu-close abs" width="16" height="16" viewBox="0 0 16 16" aria-label="Close menu"><path d="M2 2L14 14M14 2L2 14" stroke="#8a968c" stroke-width="3"/></svg>
    <ul class="menu-list">
      <li class="active">Home</li><li>About us</li><li>Packages</li><li>Pricing</li><li>Gallery</li><li>What makes us Unique</li><li>Contact us</li>
    </ul>
  </nav>
</header>

<section class="hero abs" role="img" aria-label="Photo of a bride and groom embracing on a sunlit porch">
  <div class="hero-caption abs">
    <div class="hero-title abs">WEDDING AND EVENT VENUE</div>
    <div class="hero-sub abs">Neque porro quisquam est qui</div>
  </div>
  <div class="slider-arrows abs">
    <span><svg width="10" height="10" viewBox="0 0 10 10"><path d="M6.5 1.5L3 5l3.5 3.5" fill="none" stroke="#fff" stroke-width="2"/></svg></span>
    <span><svg width="10" height="10" viewBox="0 0 10 10"><path d="M3.5 1.5L7 5 3.5 8.5" fill="none" stroke="#fff" stroke-width="2"/></svg></span>
  </div>
</section>

<section class="intro-band abs">
  <p class="intro-text abs">It is a long established fact that a reader will be distracted by the readable content of a page when looking at its layout. The point of using Lorem Ipsum is that it has a more-or-less normal distribution of letters, as opposed to using 'Content here.</p>
  <div class="btn-contact abs">CONTACT NOW</div>
</section>

<section class="packages abs wood">
  <h2 class="section-title abs" style="top:70px;font-weight:400">Our Packages</h2>
  <article class="package-card abs" style="left:106px">
    <div class="package-photo abs" role="img" aria-label="Photo of guests dancing at an evening reception" style="background:linear-gradient(135deg,#1e2236,#4a3e52 50%,#2a2a3a)"></div>
    <h3 class="package-name abs" style="font-weight:400">Porro quisquam</h3>
    <p class="package-text abs">It has survived not only five centuries, but also the leap into electronic typesetting,</p>
    <div class="package-more abs">Read More »</div>
  </article>
  <article class="package-card abs" style="left:446px">
    <div class="package-photo abs" role="img" aria-label="Photo of white reception tables set under trees" style="background:linear-gradient(180deg,#5f7a4a,#9eb08a 45%,#e8ece8)"></div>
    <h3 class="package-name abs" style="font-weight:400">Dolorem ipsum</h3>
    <p class="package-text abs">It has survived not only five centuries, but also the leap into electronic typesetting,</p>
    <div class="package-more abs">Read More »</div>
  </article>
  <article class="package-card abs" style="left:786px">
    <div class="package-photo abs" role="img" aria-label="Photo of a table setting with glasses and napkins" style="background:linear-gradient(135deg,#d6dcea,#f4f4f6 50%,#c8cedc)"></div>
    <h3 class="package-name abs" style="font-weight:400">Neque porro</h3>
    <p class="package-text abs">It has survived not only five centuries, but also the leap into electronic typesetting,</p>
    <div class="package-more abs">Read More »</div>
  </article>
</section>

<section class="about abs">
  <div class="about-photo abs" role="img" aria-label="Photo of a wedding party walking down an outdoor aisle"></div>
  <div class="about-box text-box abs">
    <h2 class="box-title abs" style="left:40px;top:32px;font-weight:400">About us</h2>
    <p class="box-text abs" style="left:40px;top:78px;width:440px">It is a long established fact that a reader will be distracted by the readable content of a page when looking at its layout. The point of using Lorem Ipsum is that it has a more-or-less normal distribution of letters, as opposed to using 'Content here,</p>
    <div class="btn-small abs" style="left:39px;top:184px;width:102px;background:var(--sage-dark)">Read More</div>
  </div>
</section>

<section class="testimonial abs wood">
  <p class="quote-text abs">It has survived not only five centuries, but also the leap into electronic typesetting, remaining essentially unchanged. It was popularised in the 1960s with the release of Letraset sheets containing Lorem Ipsum passages,</p>
  <div class="quote-author abs">- Porro quisquam</div>
</section>

<section class="unique abs">
  <div class="unique-photo abs" role="img" aria-label="Photo of a bridesmaid helping another with her red dress"></div>
  <div class="unique-box text-box abs">
    <h2 class="box-title abs" style="right:46px;top:36px;font-weight:400">What makes us Unique</h2>
    <p class="box-text abs" style="right:46px;top:82px;width:440px;font-size:13.5px">It is a long established fact that a reader will be distracted by the readable content of a page when looking at its layout. The point of using Lorem Ipsum is that it has a more-or-less normal distribution of letters, as opposed to using 'Content here,</p>
    <div class="btn-small abs" style="left:361px;top:186px;width:104px;background:var(--gold-dark)">Read More</div>
  </div>
</section>

<footer class="site-footer abs">
  <div class="footer-brand abs">Maplecrest Cove Retreat</div>
  <nav class="footer-nav abs">Home<span class="sep">|</span>About us<span class="sep">|</span>Pricing<span class="sep">|</span>FAQ<span class="sep">|</span>Contact us</nav>
  <div class="footer-social abs" aria-label="Social links"><span></span><span></span><span></span></div>
  <div class="copyright abs">Copyright © 2017 All Rights Reserved</div>
</footer>

</body>
</html>
```